maplecrest gymnastics academy

need a website for above to contain information about the academy, enrollment form etc..

Need a web design for new business Maplecrest Gymnastics Academy offering classes in gymnastics. Info on the business is in the doc called "Web design" which details the tabs I will need on my page. Please see our ClubHub page to get an idea of the style Maplecrestgymnasticsacademy.

Thank you for your help. I do not require hosting of a domain name just need it all ready to be hosted. Thanks

Budget now increased to include the coding of the website as well.

```html
<!DOCTYPE html>
<html lang="en">
<head>
<meta charset="utf-8">
<title>Maplecrest Gymnastics Academy</title>
<link href="https://fonts.googleapis.com/css2?family=Roboto+Condensed:wght@400;700&family=Open+Sans:ital,wght@0,300;0,400;0,600;0,700;1,400&display=swap" rel="stylesheet">
<style>
  :root {
    --bg: #222222;
    --panel: #1c1c1c;
    --gold: #c2ab58;
    --gold-btn: #b4a35c;
    --text: #d2d2d2;
    --muted: #a9a9a9;
    --white: #ffffff;
    --line: #3a3a3a;
    --social-blue: #3b5a9a;
    --logo-yellow: #e1cf16;
    --icon-grey: #8d8d8d;
  }
  * { margin: 0; padding: 0; box-sizing: border-box; }
  html, body { width: 1191px; height: 1200px; overflow: hidden; }
  body {
    background: var(--bg);
    font-family: Arial, Helvetica, sans-serif;
    color: var(--text);
    position: relative;
  }
  .abs { position: absolute; }
  .condensed { font-family: "Roboto Condensed", "Arial Narrow", sans-serif; }

  /* Header */
  .brand {
    left: 173px; top: 13px; width: 99px; height: 109px;
    background: var(--logo-yellow);
    border: 3px solid #555;
    border-radius: 6px;
    display: flex; align-items: center; justify-content: center;
  }
  .brand-name {
    font-family: "Roboto Condensed", sans-serif;
    font-weight: 700; font-size: 14px; color: #111; text-align: center; line-height: 1.15;
  }
  .call-icon { left: 810px; top: 32px; width: 38px; height: 38px; }
  .call-text {
    left: 863px; top: 40px; font-size: 15.5px; color: var(--gold); letter-spacing: 0.2px;
  }
  .main-nav { left: 506px; top: 88px; height: 36px; display: flex; }
  .main-nav a {
    position: absolute; top: 0; height: 36px; line-height: 36px;
    color: var(--white); text-decoration: none; font-size: 13px; white-space: nowrap;
    font-family: "Roboto Condensed", sans-serif;
  }
  .main-nav a.active { background: var(--gold-btn); color: #1e1e1e; width: 74px; text-align: center; left: 0; }

  /* Hero */
  .hero {
    left: 171px; top: 137px; width: 850px; height: 358px; overflow: hidden;
  }
  .hero-photo {
    position: absolute; inset: 0;
    background:
      radial-gradient(ellipse 32% 55% at 74% 45%, rgba(190,40,45,0.75), rgba(190,40,45,0) 70%),
      radial-gradient(ellipse 60% 40% at 30% 90%, rgba(130,70,60,0.5), rgba(0,0,0,0) 70%),
      linear-gradient(180deg, #0c1a2c 0%, #1f3048 45%, #3b3a44 100%);
  }
  .hero-title { left: 50px; top: 93px; font-size: 27px; color: var(--gold); }
  .hero-sub { left: 52px; top: 135px; font-size: 30px; color: var(--white); font-weight: 700; }
  .hero-tag { left: 53px; top: 180px; font-family: "Open Sans", sans-serif; font-weight: 300; font-size: 23px; color: var(--white); }
  .hero-btn {
    left: 55px; top: 228px; width: 128px; height: 44px; background: var(--gold-btn);
    color: #1c1c1c; font-size: 15px; text-align: center; line-height: 44px;
  }
  .hero-arrows { left: 785px; top: 319px; display: flex; gap: 1px; }
  .hero-arrows span {
    width: 25px; height: 24px; background: rgba(70,70,70,0.8);
    display: flex; align-items: center; justify-content: center;
  }

  /* Content */
  .section-title { font-size: 19.5px; color: var(--gold); font-family: "Roboto Condensed", sans-serif; }
  .welcome-title { left: 173px; top: 528px; }
  .welcome-text { left: 173px; top: 565px; width: 840px; font-size: 10.8px; line-height: 22px; }

  .col-title { font-size: 17.5px; }
  .videos-title { left: 173px; top: 650px; }
  .videos-text { left: 174px; top: 685px; width: 280px; font-size: 10.8px; line-height: 20.5px; }
  .video { left: 172px; top: 734px; width: 279px; height: 207px; background: #111; }
  .video-frame {
    position: absolute; left: 0; top: 0; width: 279px; height: 186px;
    background:
      radial-gradient(ellipse 40% 30% at 40% 45%, rgba(40,60,140,0.7), rgba(0,0,0,0) 70%),
      linear-gradient(180deg, #3a3226 0%, #2a2620 60%, #1b1a18 100%);
  }
  .play {
    position: absolute; left: 106px; top: 60px; width: 66px; height: 66px; border-radius: 50%;
    background: rgba(80,80,80,0.6);
  }
  .controls {
    position: absolute; left: 0; bottom: 0; width: 279px; height: 21px;
    background: #1a1a1a; border-top: 1px solid #333; font-size: 8.5px; color: #ddd;
  }

  .gallery-title { left: 481px; top: 650px; }
  .gallery-arrows { left: 712px; top: 655px; font-size: 11px; color: var(--muted); letter-spacing: 6px; }
  .gallery-photo {
    left: 484px; top: 690px; width: 249px; height: 208px; border: 3px solid #3a3a3a;
    background:
      radial-gradient(ellipse 35% 45% at 55% 50%, rgba(50,70,160,0.6), rgba(0,0,0,0) 70%),
      linear-gradient(160deg, #2c2c2c 0%, #181818 100%);
  }
  .gallery-text { left: 483px; top: 910px; width: 250px; font-size: 10.8px; line-height: 20.5px; }

  .about-title { left: 769px; top: 656px; }
  .about-text { left: 769px; top: 693px; width: 255px; font-size: 10.6px; line-height: 19.6px; }
  .about-list { left: 769px; top: 819px; width: 255px; list-style: none; font-size: 10.6px; line-height: 21px; }
  .about-list li { position: relative; padding-left: 16px; margin-bottom: 7px; }
  .about-list svg { position: absolute; left: 0; top: 6px; }

  /* Band */
  .band {
    left: 170px; top: 987px; width: 850px; height: 96px; background: var(--panel); border: 1px solid var(--line);
  }
  .band-text {
    position: absolute; left: 29px; top: 24px; width: 500px; font-style: italic;
    font-size: 12.4px; line-height: 26px; color: var(--text);
  }
  .band-btn {
    position: absolute; left: 556px; top: 19px; width: 274px; height: 57px; background: var(--social-blue);
    border-radius: 2px; display: flex; align-items: center; justify-content: center; gap: 12px;
    font-family: "Open Sans", sans-serif; font-weight: 700; font-size: 14.5px; color: var(--white);
  }
  .band-btn i { width: 12px; height: 12px; background: var(--white); display: block; }

  /* Footer */
  .footer-nav { left: 176px; top: 1119px; font-family: "Open Sans", sans-serif; font-size: 9.6px; color: var(--muted); word-spacing: 1px; }
  .footer-nav span.sep { padding: 0 16px; }
  .copyright { left: 176px; top: 1149px; font-family: "Open Sans", sans-serif; font-size: 9.4px; color: var(--muted); }
  .social-label { left: 653px; top: 1134px; font-family: "Open Sans", sans-serif; font-size: 9.4px; color: var(--muted); }
  .social { left: 840px; top: 1125px; display: flex; gap: 8px; }
  .social span { width: 28px; height: 28px; border-radius: 50%; background: var(--icon-grey); display: block; }
</style>
</head>
<body>

<header>
  <div class="abs brand"><span class="brand-name">MAPLECREST</span></div>
  <svg class="abs call-icon" viewBox="0 0 38 38" aria-hidden="true">
    <circle cx="19" cy="19" r="17.5" fill="none" stroke="#c2ab58" stroke-width="1.6"/>
    <path d="M14 10c-2 1-3 3-2.5 6 1 5 5 10 9 12 2 1 4 0 5-1l-3-4-2 1c-2-1-4-4-4.5-6l2-1.5L15 10z" fill="none" stroke="#c2ab58" stroke-width="1.5" stroke-linejoin="round"/>
  </svg>
  <div class="abs call-text condensed">CALL US : ( 2417 ) 305 118</div>
  <nav class="abs main-nav">
    <a class="active" href="#">HOME</a>
    <a href="#" style="left:116px">FORMS</a>
    <a href="#" style="left:216px">MORE INFO</a>
    <a href="#" style="left:335px">POLICIES</a>
    <a href="#" style="left:444px">CONTACT US</a>
  </nav>
</header>

<section class="abs hero">
  <div class="hero-photo" role="img" aria-label="Gymnast in a red leotard leaping mid-air in a split jump in front of a stadium crowd"></div>
  <div class="abs hero-title condensed">MAPLECREST GYMNASTICS ACADEMY</div>
  <div class="abs hero-sub condensed">GYM · SPORTS CLUB</div>
  <div class="abs hero-tag">HOLISTIC GYMNASTICS COACHING</div>
  <div class="abs hero-btn condensed">VIEW DETAILS</div>
  <div class="abs hero-arrows">
    <span><svg width="8" height="12" viewBox="0 0 8 12"><path d="M7 1 2 6l5 5" fill="none" stroke="#999" stroke-width="1.3"/></svg></span>
    <span><svg width="8" height="12" viewBox="0 0 8 12"><path d="M1 1l5 5-5 5" fill="none" stroke="#999" stroke-width="1.3"/></svg></span>
  </div>
</section>

<main>
  <h1 class="abs section-title welcome-title">WELCOME TO MAPLECREST GYMNASTICS ACADEMY</h1>
  <p class="abs welcome-text">Welcome to Maplecrest Gymnastics Academy (MGA),&nbsp; Gymnastics is for everyone, people of all ages, shapes, sizes and capabilities can participate in and enjoy gymnastics, We offer classes from Kindergym to Adult classes&nbsp; MGA is GYMSTATE Affiliated club and our coaches are accredited and qualified with National Gymnastics Federation.</p>

  <h2 class="abs section-title col-title videos-title">OUR VIDEOS</h2>
  <p class="abs videos-text">MGA is newly established family business whose mission is to provide high quality gymnastics program...</p>
  <div class="abs video">
    <div class="video-frame" role="img" aria-label="Video still of a gymnast in a blue leotard performing on the uneven bars"></div>
    <div class="play"><svg width="66" height="66" viewBox="0 0 66 66"><path d="M27 22v22l18-11z" fill="#ddd"/></svg></div>
    <div class="controls">
      <svg class="abs" style="left:8px;top:5px" width="9" height="11"><rect x="0" y="0" width="3" height="11" fill="#bbb"/><rect x="5" y="0" width="3" height="11" fill="#bbb"/></svg>
      <svg class="abs" style="left:30px;top:5px" width="20" height="11"><path d="M0 4h3l4-4v11L3 7H0z" fill="#888"/><rect x="10" y="6" width="1.5" height="5" fill="#888"/><rect x="13" y="4" width="1.5" height="7" fill="#888"/><rect x="16" y="2" width="1.5" height="9" fill="#888"/></svg>
      <span class="abs" style="left:55px;top:5px">0:04 / 0:30</span>
      <div class="abs" style="left:113px;top:8px;width:100px;height:5px;background:#000"></div>
      <div class="abs" style="left:113px;top:8px;width:42px;height:5px;background:#555"></div>
      <div class="abs" style="left:113px;top:8px;width:6px;height:5px;background:#c22"></div>
      <div class="abs" style="left:116px;top:5px;width:11px;height:11px;border-radius:50%;background:#ccc"></div>
      <svg class="abs" style="left:259px;top:5px" width="11" height="11"><path d="M0 3V0h3M8 0h3v3M11 8v3H8M3 11H0V8" fill="none" stroke="#777" stroke-width="1.2"/></svg>
    </div>
  </div>

  <h2 class="abs section-title col-title gallery-title">OUR GALLERY</h2>
  <div class="abs gallery-arrows">‹ ›</div>
  <div class="abs gallery-photo" role="img" aria-label="Gymnast in a sparkling blue leotard performing a move on the balance beam"></div>
  <p class="abs gallery-text">MGA is newly established family business whose mission is to provide high quality...</p>

  <h2 class="abs section-title col-title about-title">ABOUT MGA</h2>
  <p class="abs about-text">MGA is newly established family business whose mission is to provide high quality gymnastics program in a wide variety actrivities to suit all ages, levels and ability. Our vision is to become one of the most successful and holistic gymnastics club in Sydney. Our aim is to provide</p>
  <ul class="abs about-list">
    <li><svg width="10" height="8"><path d="M1 4l3 3 5-6" fill="none" stroke="#9bbf2e" stroke-width="1.6"/></svg>A family friendly and supportive environment forall gymnasts to enjoy</li>
    <li><svg width="10" height="8"><path d="M1 4l3 3 5-6" fill="none" stroke="#9bbf2e" stroke-width="1.6"/></svg>High quality, dedicated and motivated coaches</li>
    <li><svg width="10" height="8"><path d="M1 4l3 3 5-6" fill="none" stroke="#9bbf2e" stroke-width="1.6"/></svg>Progressive and enjoyable recreational and Competitive gymnastics programs</li>
  </ul>

  <section class="abs band">
    <p class="band-text">MGA is newly established family business whose mission is to provide high quality gymnastics program in a wide variety activrities to suit all ages, levels and ability.</p>
    <div class="band-btn"><i></i>CONNECT WITH CLUBHUB</div>
  </section>
</main>

<footer>
  <div class="abs footer-nav">HOME<span class="sep">/</span>FORMS<span class="sep">/</span>MORE INFO<span class="sep">/</span>POLICIES<span class="sep">/</span>CONTACT US</div>
  <div class="abs copyright">© COPYRIGHT 2014. MAPLECREST GYMNASTICS ACADEMY. ALL RIGHTS RESERVED.</div>
  <div class="abs social-label">CONNECT WITH OUR SOCIAL NETWORK :</div>
  <div class="abs social"><span></span><span></span><span></span><span></span><span></span></div>
</footer>

</body>
</html>
```